The logo name is "Harbor Skin". The name of the product will be "Cutaneous Comfort". This product is specifically formulated for amputees. Therefore under the product name it should state "for amputees". The catch phrase will be "Experience Harbor find Calmness"
These are the things we need on the label:
Logo, product name, "for amputees", "Experience Harbor find Calmness", Safe, Effective, Directions: spray on problem areas, no need to dry off. harborskin.example, Made in Canada, 500ml.
The MOST IMPORTANT and therefore the most prominent thing on this lable will be the LOGO! The second most prominent thing will be the word "Comfort" We want to keep it very plain, very simple, very unclutered. Keep in mind that this lable will be placed on a white bottle or have a white back ground. The 500ml white PE bottle with trigger sprayer will have a tear drop label. See attached die line (S-294).
We want to stay with the colours that goes with the colour scheme of the logo. See attached logo. Soft colours. We do not want a picture! We would like the lable to be classy and rich.
Updates
The logo name is "Harbor Skin". The name of the product will be "Cutaneous Comfort". This product is specificlly formulated for amputees. Therefore under the product name it should state "for amputees". The catch phrase will be "Experience Harbor find Calmness"
Logo, product name, "for amputees", catch phrase "Experience Harbor find Calmness", Clean, Safe, Effective, Directions: spray on problem areas, no need to dry off. Also Harbor Skin Corpation, harborskin.example, Made in Canada, 500ml.
We want to stay with the colour scheme of the logo. See attached logo. Soft colours. We do not want a picture! We would like the lable to be classy and rich.
This is the offical directive that came from the governing panal of this lable. This panal it not know where it wanted to take this lable that would represent this line until they review all of your submissions, thank you for all your talented hard work. But now it is clear it is time to regroup and hit this objective.
Project Deadline Extended
Reason: New restrictions on lable wording for this product.
Target Market(s)
Amputees and Parents of.
Industry/Entity Type
Product
Requirements
Must have
- Final product to be in a pdf or an illustrator file

```html
<!DOCTYPE html>
<html lang="en">
<head>
<meta charset="utf-8">
<title>Harbor Skin – Cutaneous Comfort Label</title>
<link rel="stylesheet" href="https://fonts.googleapis.com/css2?family=Cinzel:wght@400;700;900&family=Roboto+Condensed:ital,wght@0,400;0,700;1,700;1,900&display=swap">
<style>
  :root{
    --page:#f1f1f1;
    --cream:#fff8ea;
    --peach:#fde0b2;
    --orange:#f7b55a;
    --orange-soft:#fbd08e;
    --teal:#bfe3e4;
    --teal-line:#a9d9da;
    --green:#0d5a46;
    --green-dark:#0a4637;
    --white:#ffffff;
  }
  html,body{margin:0;padding:0;overflow:hidden;}
  body{width:1200px;height:1000px;background:var(--page);}
  .label{display:block;width:1200px;height:1000px;}
  .brand-name{font-family:"Cinzel",serif;font-weight:700;fill:var(--green);}
  .product-line{font-family:"Roboto Condensed",sans-serif;font-weight:700;fill:var(--white);letter-spacing:6px;}
  .product-name{font-family:"Cinzel",serif;font-weight:900;fill:var(--green);stroke:var(--white);stroke-width:5px;paint-order:stroke;}
  .audience-for{font-family:"Roboto Condensed",sans-serif;font-weight:700;fill:var(--green);}
  .audience{font-family:"Roboto Condensed",sans-serif;font-style:italic;font-weight:900;fill:var(--green);}
  .tagline{font-family:"Roboto Condensed",sans-serif;font-weight:700;fill:var(--green);}
  .claims{font-family:"Cinzel",serif;font-weight:400;fill:var(--green-dark);}
  .small{font-family:"Roboto Condensed",sans-serif;fill:var(--green-dark);}
  .small-head{font-style:italic;font-weight:700;}
  .small-bold{font-weight:700;}
  .web{font-family:"Roboto Condensed",sans-serif;font-weight:700;fill:var(--green-dark);letter-spacing:2.5px;}
</style>
</head>
<body>
<svg class="label" viewBox="0 0 1200 1000" xmlns="http://www.w3.org/2000/svg" role="img" aria-label="Harbor Skin Cutaneous Comfort tear drop label">
  <defs>
    <radialGradient id="label-fill" cx="50%" cy="58%" r="62%">
      <stop offset="0%" stop-color="var(--cream)"/>
      <stop offset="60%" stop-color="#fff0d6"/>
      <stop offset="100%" stop-color="var(--peach)"/>
    </radialGradient>
    <linearGradient id="band-fill" x1="0" y1="0" x2="0" y2="1">
      <stop offset="0%" stop-color="var(--orange-soft)"/>
      <stop offset="50%" stop-color="var(--orange)"/>
      <stop offset="100%" stop-color="var(--orange-soft)"/>
    </linearGradient>
    <clipPath id="label-clip">
      <path d="M600,50 C680,150 832,330 832,560 L832,870 Q832,950 752,950 L448,950 Q368,950 368,870 L368,560 C368,330 520,150 600,50 Z"/>
    </clipPath>
  </defs>

  <!-- label die shape -->
  <path class="label-shape" d="M600,50 C680,150 832,330 832,560 L832,870 Q832,950 752,950 L448,950 Q368,950 368,870 L368,560 C368,330 520,150 600,50 Z" fill="url(#label-fill)"/>

  <g clip-path="url(#label-clip)">
    <!-- product band -->
    <path class="band-line-top" d="M340,440 Q600,380 860,420" fill="none" stroke="var(--teal-line)" stroke-width="10"/>
    <path class="band" d="M340,462 Q600,402 860,440 L860,600 Q600,640 340,612 Z" fill="url(#band-fill)"/>
    <path class="band-line-bottom" d="M340,626 Q600,654 860,612" fill="none" stroke="var(--teal-line)" stroke-width="8"/>
  </g>

  <!-- brand -->
  <rect class="brand-mark" x="398" y="260" width="46" height="46" fill="var(--teal)"/>
  <text class="brand-name" x="456" y="300" font-size="40">Harbor Skin</text>

  <!-- product -->
  <text class="product-line" x="600" y="446" font-size="26" text-anchor="middle">Cutaneous</text>
  <text class="product-name" x="600" y="545" font-size="84" text-anchor="middle" textLength="390" lengthAdjust="spacingAndGlyphs">COMFORT</text>
  <text class="audience-for" x="600" y="578" font-size="22" text-anchor="middle">For</text>
  <text class="audience" x="600" y="609" font-size="34" text-anchor="middle">AMPUTEES</text>

  <!-- tagline and claims -->
  <text class="tagline" x="600" y="692" font-size="27" text-anchor="middle">Experience Harbor find Calmness</text>
  <rect class="claims-box" x="486" y="716" width="228" height="58" fill="var(--teal)"/>
  <text class="claims" x="600" y="741" font-size="19" text-anchor="middle">CLEAN, SAFE</text>
  <text class="claims" x="600" y="765" font-size="19" text-anchor="middle">&amp; EFFECTIVE</text>

  <!-- directions and maker -->
  <text class="small small-head" x="600" y="792" font-size="12" text-anchor="middle">Directions:</text>
  <text class="small" x="600" y="808" font-size="12" text-anchor="middle">Spray on problem areas, no need to dry off.</text>
  <text class="small small-head" x="600" y="834" font-size="12" text-anchor="middle">Manufactured by:</text>
  <text class="small" x="600" y="850" font-size="12" text-anchor="middle">Harbor Skin Corpation</text>
  <text class="web" x="600" y="878" font-size="13" text-anchor="middle">www.harborskin.example</text>
  <text class="small" x="600" y="904" font-size="12" text-anchor="middle">Made in Canada  |  500mL</text>
</svg>
</body>
</html>
```